Modern & Fresh Vantacor Book Cover

Need a creative e-book cover for my book.

Title: Master Vantacor Fast
Subtitle: Learn How To Easily Choose & Enroll in the Perfect Coverage at the Perfect Time.

Target Market(s)

60-70 year olds in the United States

Font styles to use
Sans Serif

Colors
9bcb3c
33a6d7

Requirements
Must have
• Must look modern and fresh.
• Use our company colors www.Movaquill.com

```html
<!DOCTYPE html>
<html lang="en">
<head>
<meta charset="utf-8">
<title>Master Vantacor Fast – Book Cover</title>
<link rel="stylesheet" href="https://fonts.googleapis.com/css2?family=Anton&family=Bebas+Neue&family=Montserrat:wght@400;800&display=swap">
<style>
  :root {
    --paper: #ffffff;
    --brand-blue: #2c7bbd;
    --rule-blue: #4f8fca;
    --brand-green: #7dac3b;
    --ink-grey: #444444;
    --art-light: #eef1f4;
    --art-mid: #d4d8dc;
  }
  html, body {
    margin: 0;
    padding: 0;
    width: 800px;
    height: 1200px;
    overflow: hidden;
    background: var(--paper);
  }
  .cover {
    display: block;
    width: 800px;
    height: 1200px;
  }
  .kicker {
    font-family: "Montserrat", sans-serif;
    font-weight: 800;
    fill: var(--brand-blue);
  }
  .kicker-rule {
    stroke: var(--rule-blue);
    stroke-width: 4;
  }
  .title-middle {
    font-family: "Anton", sans-serif;
    fill: var(--brand-green);
  }
  .title-main {
    font-family: "Anton", sans-serif;
    fill: var(--brand-blue);
  }
  .subtitle {
    font-family: "Montserrat", sans-serif;
    font-weight: 400;
    font-size: 21px;
    letter-spacing: 0.6px;
    fill: var(--ink-grey);
  }
  .author {
    font-family: "Bebas Neue", sans-serif;
    font-size: 60px;
    fill: var(--brand-blue);
  }
</style>
</head>
<body>
<svg class="cover" viewBox="0 0 800 1200" xmlns="http://www.w3.org/2000/svg">
  <defs>
    <radialGradient id="art-fill" cx="0.55" cy="0.5" r="0.55">
      <stop offset="0" stop-color="#eef1f4"/>
      <stop offset="1" stop-color="#d4d8dc"/>
    </radialGradient>
  </defs>

  <rect class="paper" width="800" height="1200" fill="var(--paper)"/>

  <g class="title-block">
    <line class="kicker-rule" x1="93" y1="112" x2="228" y2="112"/>
    <text class="kicker" x="240" y="146" font-size="96" textLength="320" lengthAdjust="spacingAndGlyphs">MASTER</text>
    <line class="kicker-rule" x1="572" y1="112" x2="703" y2="112"/>

    <text class="title-middle" x="81" y="307" font-size="156" textLength="637" lengthAdjust="spacingAndGlyphs">VANTACOR</text>
    <text class="title-main" x="81" y="597" font-size="317" textLength="638" lengthAdjust="spacingAndGlyphs">FAST</text>
  </g>

  <g class="subtitle-block">
    <text class="subtitle" x="400" y="642" text-anchor="middle">Learn How To Easily Choose &amp; Enroll in the Perfect</text>
    <text class="subtitle" x="400" y="671" text-anchor="middle">Coverage at the Perfect Time.</text>
  </g>

  <rect class="cover-art" x="224" y="716" width="351" height="359" rx="18"
        fill="url(#art-fill)" role="img"
        aria-label="Illustration of a businessman tracing a red path through a circular maze to a green check mark at its centre"/>

  <text class="author" x="226" y="1156" textLength="348" lengthAdjust="spacing">AUTHOR NAME</text>
</svg>
</body>
</html>
```